New Business Card Design Project

Use the flyer uploaded and website www.brightoakbuilders.com for inspiration.
List Our Services on Backside of business cards
Marcus Delling
Harborline Builders Inc.
Licensed General Contractors
858-471-6093

Contact Information for Business Card

Use the flyer uploaded and website www.brightoakbuilders.com for inspiration. List Our Services on Backside of business cards Marcus Delling Harborline Builders Inc. Licensed General Contractors 858-471-6093

```html
<!DOCTYPE html>
<html lang="en">
<head>
<meta charset="utf-8">
<title>Harborline Builders – Business Card</title>
<link href="https://fonts.googleapis.com/css2?family=Roboto:wght@400;700&family=Roboto+Condensed:wght@400;700&display=swap" rel="stylesheet">
<style>
  :root {
    --page-bg: #2b2b2b;
    --card-bg: #333333;
    --card-edge: #3d3d3d;
    --text-main: #ffffff;
    --text-soft: #d9d9d9;
    --brand: #bdbdbd;
    --rule: #9a9a9a;
  }
  * { box-sizing: border-box; margin: 0; padding: 0; }
  html, body { width: 1200px; height: 689px; overflow: hidden; background: var(--page-bg); }
  .canvas {
    width: 1200px; height: 689px;
    display: flex; align-items: center; justify-content: center; gap: 48px;
  }
  .card {
    position: relative;
    width: 525px; height: 300px;
    background: var(--card-bg);
    border-radius: 18px;
    box-shadow: inset 0 0 0 1px var(--card-edge), 0 18px 40px rgba(0,0,0,.45);
    overflow: hidden;
    font-family: "Roboto", Arial, sans-serif;
    color: var(--text-main);
  }

  /* Back: company name + services */
  .card-back .brand {
    position: absolute; top: 96px; left: 0; right: 0;
    text-align: center;
    font-family: "Roboto", Arial, sans-serif;
    font-weight: 400;
    font-size: 28px; letter-spacing: 2px;
    color: var(--brand);
    text-transform: uppercase;
  }
  .card-back .services {
    position: absolute; left: 16px; right: 16px; bottom: 36px;
    text-align: center;
    font-family: "Roboto Condensed", "Arial Narrow", sans-serif;
    font-size: 12px; line-height: 1.5;
    color: var(--text-soft);
  }
  .services .line { display: block; white-space: nowrap; }
  .services b { color: var(--text-main); font-weight: 700; }

  /* Front: contact details */
  .card-front .person { position: absolute; left: 40px; top: 58px; }
  .person .name {
    font-family: "Roboto Condensed", "Arial Narrow", sans-serif;
    font-size: 25px; font-weight: 700; letter-spacing: .5px;
    text-transform: uppercase;
  }
  .person .role { font-size: 13px; color: var(--text-soft); margin: 2px 0 0 14px; }
  .contacts { list-style: none; margin: 22px 0 0 14px; }
  .contacts li {
    display: flex; align-items: center; gap: 9px;
    font-size: 14px; line-height: 20px; color: var(--text-soft);
  }
  .contacts svg { width: 12px; height: 12px; fill: var(--text-main); flex: none; }
  .divider { width: 18px; height: 1px; background: var(--rule); margin: 10px 0 8px 14px; }
  .company { margin-left: 14px; font-size: 13.5px; line-height: 18px; color: var(--text-soft); }
</style>
</head>
<body>
<main class="canvas">

  <section class="card card-back" aria-label="Card back">
    <div class="brand">Harborline Builders</div>
    <p class="services">
      <span class="line"><b>Remodel :</b> Kitchen &amp; Bath | <b>Painting :</b> Interior &amp; Exterior | <b>Flooring :</b> Carpet, Vinyl, Wood</span>
      <span class="line">Window &amp; Door Replacement | <b>Plumbing :</b> Repairs &amp; Upgrades | Energy- Efficient Upgrades</span>
      <span class="line">Deck &amp; Patio Construction | Water &amp; Mold Damage | Garage Renovation</span>
    </p>
  </section>

  <section class="card card-front" aria-label="Card front">
    <div class="person">
      <h1 class="name">Marcus Delling</h1>
      <p class="role">President</p>
      <ul class="contacts">
        <li>
          <svg viewBox="0 0 24 24" aria-hidden="true"><path d="M6.6 10.8a15.1 15.1 0 0 0 6.6 6.6l2.2-2.2c.3-.3.7-.4 1-.2 1.1.4 2.3.6 3.6.6.6 0 1 .4 1 1V20c0 .6-.4 1-1 1C10.6 21 3 13.4 3 4c0-.6.4-1 1-1h3.5c.6 0 1 .4 1 1 0 1.3.2 2.5.6 3.6.1.3 0 .7-.2 1z"/></svg>
          858-471-6093
        </li>
        <li>
          <svg viewBox="0 0 24 24" aria-hidden="true"><path d="M2 5h20v14H2z M4 7v.5l8 5 8-5V7l-8 5z" fill-rule="evenodd"/></svg>
          info@brightoakbuilders.com
        </li>
        <li>
          <svg viewBox="0 0 24 24" aria-hidden="true"><circle cx="12" cy="12" r="10"/></svg>
          www.brightoakbuilders.com
        </li>
      </ul>
      <div class="divider"></div>
      <p class="company">Harborline Builders Inc.<br>Licensed General Contractors</p>
    </div>
  </section>

</main>
</body>
</html>
```